Q.B. Brightpath Store

The design is for eCommerce home page but I would like it to complement this site: http://www.qbbrightpathsolutions.com/ but... it should also have independence as a standalone site.

The best design will be able to effectively mix corporate with a high quality small business consumer feel. It should be completely custom design, not a template look or feel. I want the users to get the feeling that this is the place to go for buying tech for business. We sell the same products as RVK.

You can be creative as you wish, as long as the elements of a great eCommerce site are present.

I would like your 'design' to blow these away:
http://www.shopping.zl.com/
mirabelo.com
http://www.rvk.com/

Here are references:
Call to action
http://markvantage.com/us/blog/48153-seven-tips-for-designing-an-effective-ecommerce-call-to-action

Effective Ecommerce design
http://www.vexa.com/ss/7-tips-for-effective-e-commerce#0

91 points of ecommerce
http://qir.com/blog/holygrail-of-ecommerce-conversion-optimization-91-points-checklist

UPDATE 07/11/2013:

Please look at the category sample png files. I see already many people are using the main menu from qbbrightpathsolutions.com and I do not mind your creativiety, but this is an eCommerce store and people need a menu to get to the categories and/or product types. I don't want to limit anyone creativity by the png samples. I'm also not using them to show I like them in any particular way or form, just that it's needed, whether it's a button (dropdown of course) that says 'Categories' or 'Products, whether it an accordion, horizontal or vertical.

Thanks

UPDATE 07/12/2013:

Please find other use of space that has been used for About Us paragraph (if you've added it to the page). About Us should have it's own page and the purpose of the design should be to sell products (and some services as products). Please put a link or some other creative method to lead users to the About Us page.

Reason: I've raised the award, including 1st, 2nd, and 3rd place and participation payments so I will also extend 7 days. Thanks!

I've updated the product brief. Please scroll down to where it says: UPDATE 07/11/2013

Thanks!

UPDATE 07/12/2013:

Please find other use of space that has been used for About Us paragraph (if you've added it to the page).  About Us should have it's own page and the purpose of the design should be to sell products (and some services as products). Please put a link or some other creative method to lead users to the About Us page if you must but not on the real estate of the page.

Thanks!

Added updates to the brief 7/14/2013.

Thanks!

The voting is in and the project is complete.  Thanks everyone for joining, all of those who participated are truly amazingly talented. But, there were only 3 prizes.  I will be having further projects down the line to develop other pages to this site after the initial implementation is completed.  I truly would like to have you all back. 

- Thank you.

Target Market(s)

corporate decision-makers AND small business consumers

Industry/Entity Type

Small Business

Requirements
Must have
• Call to action.
Openness (non-clutter).

These elements:
Search box
Logo
Tagline
Telephone number
Contact details
Address
My account / sign in
Shopping basket / checkout link
Latest offers
Promotional area
Email sign up
Delivery information
About us
Link to press office / corporate site
Terms and conditions
Sitemap for the footer.
Delivery offers: free
Personalized recommendations
Social media links
Accepted payment methods
Link to blog or community section
Change language / country

http://smartplansblog.pelloware.com/sales-leads-landing-page/

UPDATE 07/14/2013
Category Menu. This can be a dropdown, horizontal, vertical, etc. But shoppers need to know how to get to the products they want to buy.
Nice to have
• Trustmarks
Blog/Blog link

UPDATE 07/12/2013:
Make the footer useful.

UPDATE 07/14/2013 (Suggestions of elements to differentiate your designs)

-Quick Shop: A quick buy module/section: Where a user can put in a SKU number or Model number to quickly add the product to their shopping cart.

-Featured
-Best Sellers
-Specials
-Trending Tags/Tag Cloud
- Activity Stream
- Cross Sell/ Up Sell
- Testimonial
- Social Network Feed
- Live Help
- Feedback/Support/Contact Tab
- Show logged in user (i.e. Welcome, Mark Pelley)
Should not have
• The design SHOULD NOT be generic like this:

http://www.artgatherly.com/design/52392
http://www.falconmart.com/

The page should not feel over cluttered. It should not have low quality icons or design elements. Navigation should not be hard to discover or confusing.

```html
<!DOCTYPE html>
<html lang="en">
<head>
<meta charset="utf-8">
<title>Q.B. Brightpath Store</title>
<link href="https://fonts.googleapis.com/css2?family=Open+Sans:ital,wght@0,400;0,600;0,700;1,400&display=swap" rel="stylesheet">
<style>
:root{
  --blue:#0b63b0;
  --blue-dark:#07508f;
  --sky:#19a4e6;
  --title:#1f74c2;
  --red:#d11414;
  --green:#8aab3c;
  --ink:#111;
  --grey:#555;
  --line:#dcdcdc;
  --bg:#fff;
  --footer-bar:#111;
}
*{box-sizing:border-box;margin:0;padding:0}
html,body{width:692px;height:1200px;overflow:hidden}
body{position:relative;background:var(--bg);font-family:"Open Sans",Arial,sans-serif;color:var(--ink);font-size:7px}
.abs{position:absolute}
.card{background:#fff;border:1px solid #e6e6e6;box-shadow:0 0 4px rgba(0,0,0,.12)}
.ph{display:block}

/* header */
.topbar{left:452px;top:0;width:240px;height:17px;background:#5d5d5d;border-bottom-left-radius:10px;color:#fff;font-size:6.5px;display:flex;align-items:center;gap:8px;padding-left:16px}
.cart-btn{border:1px solid #fff;background:#fff;color:#333;padding:1px 5px;font-weight:600}
.logo{left:55px;top:16px;display:flex;align-items:center;gap:5px}
.logo-dot{width:28px;height:28px;border-radius:50%;background:var(--blue)}
.logo-text{color:var(--blue);font-size:12px;font-weight:600;line-height:1.05;letter-spacing:.5px}
.call{left:404px;top:33px;color:var(--red);font-size:10.5px;font-weight:700;display:flex;align-items:center;gap:3px}
.search{left:545px;top:33px;width:89px;height:12px;border:1px solid #ccc;font-size:6px;color:#888;padding:1px 4px;display:flex;justify-content:space-between;align-items:center}
.nav{left:0;top:65px;width:692px;height:30px;background:var(--blue);display:flex;padding-left:55px}
.nav a{color:#fff;text-decoration:none;font-size:8.6px;font-weight:600;padding:0 10px;display:flex;align-items:center}
.nav a.active{background:var(--red)}

/* hero */
.headline{left:0;top:113px;width:692px;text-align:center;font-size:18px;font-weight:700;letter-spacing:-.3px}
.subline{left:0;top:139px;width:692px;text-align:center;font-size:8px;color:#333}
.slider{left:55px;top:171px;width:579px;height:200px}
.slide{position:absolute;top:0;text-align:center;font-size:8px}
.slide .ph{margin:0 auto}
.feature{left:202px;top:-2px;width:178px;height:200px;background:#fff;box-shadow:0 0 5px rgba(0,0,0,.25)}
.ribbon{position:absolute;left:0;top:0}
.ribbon-text{position:absolute;left:5px;top:4px;color:#fff;font-weight:700;font-size:12px;line-height:1}
.ribbon-text small{display:block;font-size:6px;font-weight:400;margin-top:2px}
.ribbon-text b{font-size:9px;font-weight:400}
.btns{display:flex;justify-content:center;gap:2px;margin-top:5px}
.btn{font-size:5.5px;color:#fff;padding:2px 5px}
.btn-red{background:var(--red)}
.btn-blue{background:var(--blue)}
.stars{font-size:6px;letter-spacing:.5px;margin-top:4px}
.arrow{width:30px;height:30px;border-radius:50%;border:1px solid #bfe2f5;display:flex;align-items:center;justify-content:center}
.arrow span{width:16px;height:16px;border-radius:50%;background:var(--sky);display:flex;align-items:center;justify-content:center}

/* promo */
.promo{top:389px;height:39px;display:flex;align-items:center;gap:6px;padding-left:20px;color:#fff}
.promo-ring{width:24px;height:24px;border:1.5px solid #fff;border-radius:50%;display:flex;align-items:center;justify-content:center}
.promo h3{font-size:12px;font-weight:600;line-height:1}
.promo p{font-size:5.5px;margin-top:1px}

/* sidebar */
.cat{left:55px;top:447px;width:93px;height:278px;background:var(--blue)}
.side-head{background:var(--red);color:#fff;font-weight:700;font-size:7.5px;height:24px;display:flex;align-items:center;padding-left:10px}
.cat ul{list-style:none}
.cat li{color:#fff;font-size:5.8px;padding:4px 5px 4px 15px;border-bottom:1px solid rgba(255,255,255,.15);position:relative;line-height:1.2}
.cat li::before{content:"";position:absolute;left:6px;top:6px;width:3px;height:3px;background:#fff;border-radius:50%}
.cat li.on{background:var(--sky)}
.blog{left:55px;top:737px;width:93px;height:132px;background:var(--blue)}
.post{display:flex;gap:5px;padding:8px 6px;color:#fff;font-size:5.8px;line-height:1.25;border-bottom:1px solid rgba(255,255,255,.15)}
.date{background:var(--sky);width:18px;height:20px;text-align:center;font-size:10px;font-weight:700;line-height:1;padding-top:2px;flex:none}
.date small{display:block;font-size:4px;font-weight:400}
.tags{left:55px;top:879px;width:93px;height:94px;padding:9px 6px;display:flex;flex-wrap:wrap;gap:3px;align-content:flex-start}
.tag{background:#999;color:#fff;font-size:5.3px;padding:1px 5px}
.tag.dark{background:#333}

/* featured */
.sec-title{left:157px;top:445px;color:var(--title);font-size:10.5px;font-weight:600}
.products{left:155px;top:468px;width:479px;height:198px;display:flex}
.product{flex:1;text-align:center;border-right:1px solid #e6e6e6;padding-top:20px}
.product:last-child{border:0}
.product .name{color:var(--title);font-size:7.6px;line-height:1.35;margin-top:8px}
.product .price{font-size:19px;font-weight:700;margin-top:4px}
.triple{top:680px;height:172px}
.activity{left:155px;width:155px;text-align:center}
.activity h4{font-size:10px;font-weight:600;margin-top:8px}
.activity p{font-size:6.2px;font-style:italic;color:#444;line-height:1.3;padding:2px 14px}
.tollfree{left:318px;width:154px}
.tollfree .lbl{font-size:6.5px;font-weight:700;margin:11px 0 0 12px}
.tollfree .num{color:var(--blue);font-size:13px;font-weight:600;margin:2px 0 0 12px;display:flex;align-items:center;gap:2px}
.tollfree .mail{color:var(--red);font-size:9.3px;font-weight:600;margin:2px 0 0 12px}
.testi{left:481px;width:153px}
.testi .who{position:absolute;left:68px;top:21px}
.testi .who b{color:var(--title);font-size:10px;font-weight:600;display:block}
.testi .who span{font-size:5.6px;color:#999;line-height:1.3;display:block}
.testi p{position:absolute;left:31px;top:72px;width:110px;font-size:6.2px;font-style:italic;color:#444;line-height:1.3}
.quote{position:absolute;font-size:18px;color:#aaa;font-weight:700;line-height:1}

/* news */
.news{left:155px;top:869px;width:479px;height:104px}
.news h4,.tw h4{font-size:10.5px;font-weight:600}
.item{display:flex;gap:5px;margin-top:6px;font-size:6.3px;line-height:1.3;color:#333}
.item b{color:#111;font-weight:600}
.item .red{color:var(--red)}
.tw{position:absolute;left:276px;top:11px;width:195px}
.tw .tw-title{color:var(--title);font-size:7.6px}
.tw .tw-body{font-size:6.5px;color:#333;line-height:1.3}

/* footer */
.footer{left:0;top:1006px;width:692px;height:162px;background:var(--blue);color:#fff}
.fcol{position:absolute;top:31px}
.fcol h5{font-size:7.3px;font-weight:600;margin-bottom:13px}
.fcol ul{list-style:none}
.fcol li{font-size:6px;margin-bottom:6px;position:relative;padding-left:8px}
.fcol li::before{content:"";position:absolute;left:0;top:2px;width:3px;height:3px;background:#fff}
.thumbs{display:grid;grid-template-columns:repeat(3,31px);gap:8px 6px}
.thumbs .ph{width:31px;height:30px;border:2px solid #fff}
.field{background:#fff;color:#555;font-size:6px;padding:4px 6px;width:90px;margin-top:8px}
.sub{background:var(--red);color:#fff;font-size:7px;font-weight:700;width:90px;text-align:center;padding:4px 0;margin-top:6px}
.fbox{background:#fff;width:129px;height:96px;color:#333;font-size:5.2px;padding:6px}
.bottom{left:0;top:1168px;width:692px;height:32px;background:var(--footer-bar);color:#fff;font-size:6px;display:flex;align-items:center;justify-content:space-between;padding:0 58px 0 55px}
.pay{display:flex;gap:3px}
.pay span{width:24px;height:14px;background:#e8e8e8;border-radius:2px}
</style>
</head>
<body>

<header>
  <div class="abs topbar"><span>SIGNIN</span><span>SIGNUP</span><span>CHECKOUT</span><span class="cart-btn">🛒 CART : 05</span></div>
  <div class="abs logo"><span class="logo-dot"></span><span class="logo-text">Q.B. BRIGHTPATH<br>SOLUTIONS</span></div>
  <div class="abs call">
    <svg width="9" height="10" viewBox="0 0 24 24"><path fill="#d11414" d="M6.6 10.8a15 15 0 0 0 6.6 6.6l2.2-2.2c.3-.3.7-.4 1-.2 1.1.4 2.3.6 3.6.6.6 0 1 .4 1 1V20c0 .6-.4 1-1 1A17 17 0 0 1 3 4c0-.6.4-1 1-1h3.5c.6 0 1 .4 1 1 0 1.3.2 2.5.6 3.6.1.3 0 .7-.2 1z"/></svg>
    CALL : +484 - 555 - 0142
  </div>
  <div class="abs search"><span>Search</span><svg width="6" height="6" viewBox="0 0 10 10"><circle cx="4" cy="4" r="3" fill="none" stroke="#777" stroke-width="1.3"/><path d="M6.3 6.3 9 9" stroke="#777" stroke-width="1.3"/></svg></div>
  <nav class="abs nav">
    <a href="#">HOME</a><a href="#" class="active">HARDWARE</a><a href="#">LICENSING</a><a href="#">MANAGEMENT</a><a href="#">TECHNOLOGY SERVICES</a><a href="#">BENEFITS</a><a href="#">BLOG</a><a href="#">CONTACT</a>
  </nav>
</header>

<h1 class="abs headline">Lorem ipsum dolor sit amet, consectetur adipisicing elit</h1>
<p class="abs subline">Excepteur sint occaecat cupidatat non proident, sunt in culpa qui officia deserunt mollit anim id est laborum.</p>

<section class="abs slider card">
  <div class="slide" style="left:55px;top:55px;width:140px">
    <div class="ph" role="img" aria-label="Laptop showing a web store" style="width:125px;height:80px;background:linear-gradient(#e9eef3,#9aa3ab)"></div>
    <p style="margin-top:12px">Cyclone Tubes</p>
  </div>
  <div class="slide feature">
    <svg class="ribbon" width="66" height="70"><polygon points="0,0 66,0 0,70" fill="#d11414"/></svg>
    <div class="ribbon-text">$1150<small>offer 10%</small><b>off</b></div>
    <div class="ph" role="img" aria-label="Tablet computer" style="width:140px;height:90px;margin-top:55px;background:linear-gradient(#3a3a3a,#111);border-radius:6px"></div>
    <p style="color:var(--title);font-size:8px;margin-top:10px">Lorem Ipsum Dolor Consectetur</p>
    <div class="btns"><span class="btn btn-red">Add to Cart</span><span class="btn btn-blue">More Detail</span></div>
    <div class="stars">★★★★★</div>
  </div>
  <div class="slide" style="left:410px;top:45px;width:120px">
    <div class="ph" role="img" aria-label="Stack of smartphones" style="width:100px;height:95px;background:linear-gradient(#555,#111);border-radius:8px"></div>
    <p style="margin-top:8px">Pocket-Vac</p>
  </div>
  <div class="abs arrow" style="left:-15px;top:85px"><span><svg width="6" height="6" viewBox="0 0 6 6"><path d="M4 0 1 3l3 3" fill="#fff"/></svg></span></div>
  <div class="abs arrow" style="left:565px;top:85px"><span><svg width="6" height="6" viewBox="0 0 6 6"><path d="M2 0l3 3-3 3" fill="#fff"/></svg></span></div>
</section>

<div class="abs promo" style="left:55px;width:188px;background:var(--green)">
  <div class="promo-ring"><svg width="12" height="12" viewBox="0 0 12 12"><rect x="1" y="5" width="10" height="6" fill="none" stroke="#fff"/><rect x="0.5" y="3" width="11" height="2" fill="#fff"/><path d="M6 3v8" stroke="#fff"/></svg></div>
  <div><h3>SPECIAL OFFER</h3><p>UP TO 20% OFF ON COLLECTION</p></div>
</div>
<div class="abs promo" style="left:252px;width:187px;background:var(--blue)">
  <div class="promo-ring"><svg width="12" height="12" viewBox="0 0 12 12"><rect x="2" y="1" width="8" height="8" rx="1" fill="none" stroke="#fff"/><path d="M2 5h8" stroke="#fff"/><circle cx="4" cy="10.5" r="1" fill="#fff"/><circle cx="8" cy="10.5" r="1" fill="#fff"/></svg></div>
  <div><h3>FREE SHIPPING</h3><p>LOREM IPSUM DOLOR SIT AMET</p></div>
</div>
<div class="abs promo" style="left:447px;width:187px;background:var(--red)">
  <div class="promo-ring"><svg width="12" height="12" viewBox="0 0 12 12"><circle cx="6" cy="4" r="2.3" fill="#fff"/><path d="M1.5 11a4.5 4 0 0 1 9 0z" fill="#fff"/></svg></div>
  <div><h3>BEST SELLER</h3><p>UP TO 20% OFF ON COLLECTION</p></div>
</div>

<aside class="abs cat">
  <div class="side-head">Product Categories</div>
  <ul>
    <li>Lorem Ipsum</li>
    <li class="on">Lorem Ipsum<br>Dummt Category Text</li>
    <li>Lorem Ipsum<br>Dummy Category</li>
    <li>Lorem Ipsum</li>
    <li>Dummy Category</li>
    <li>Lorem Ipsum</li>
    <li>Lorem Ipsum<br>Dummy Lorem Ipsum</li>
    <li>Tempest Blower<br>Driven Airknife</li>
    <li>Lorem Ipsum<br>Dummy Categor<br>Standard Text</li>
    <li>Lorem Ipsum</li>
    <li>Dummy Text</li>
  </ul>
</aside>

<aside class="abs blog">
  <div class="side-head">Recent Blog</div>
  <div class="post"><div class="date">15<small>JULY</small></div><div>Consec elit tetur adipisicing elit Lorem ipsum dolor sit...</div></div>
  <div class="post" style="border:0"><div class="date">15<small>JULY</small></div><div>Consec elit tetur adipisicing elit Lorem ipsum dolor sit...</div></div>
</aside>

<aside class="abs tags card">
  <span class="tag">Lorem</span><span class="tag dark">Dummy Tag</span>
  <span class="tag">Dummy Tag</span><span class="tag">Lorem</span>
  <span class="tag">Lorem</span><span class="tag">Dummy Tag</span>
  <span class="tag">Dummy Tag</span><span class="tag">Ipsum</span>
  <span class="tag">Lorem</span><span class="tag">Dummy Tag</span>
  <span class="tag">Dummy Tag</span><span class="tag">Lorem</span>
</aside>

<h2 class="abs sec-title">Our Featured Products</h2>
<section class="abs products card">
  <div class="product">
    <div class="ph" role="img" aria-label="Smartphone" style="width:70px;height:62px;margin:0 auto;background:linear-gradient(135deg,#666,#111);border-radius:6px"></div>
    <p class="name">Lorem Ipsum<br>Dolor Consectetur</p><p class="price">$1150</p>
    <div class="btns"><span class="btn btn-red">Add to Cart</span><span class="btn btn-blue">More Detail</span></div><div class="stars">★★★★★</div>
  </div>
  <div class="product">
    <div class="ph" role="img" aria-label="White smartphone" style="width:70px;height:62px;margin:0 auto;background:linear-gradient(135deg,#eef2f6,#b7c3cf);border-radius:6px"></div>
    <p class="name">Lorem Ipsum<br>Dolor Consectetur</p><p class="price">$1050</p>
    <div class="btns"><span class="btn btn-red">Add to Cart</span><span class="btn btn-blue">More Detail</span></div><div class="stars">★★★★★</div>
  </div>
  <div class="product">
    <div class="ph" role="img" aria-label="Smartphone" style="width:70px;height:62px;margin:0 auto;background:linear-gradient(135deg,#666,#111);border-radius:6px"></div>
    <p class="name">Lorem Ipsum<br>Dolor Consectetur</p><p class="price">$1000</p>
    <div class="btns"><span class="btn btn-red">Add to Cart</span><span class="btn btn-blue">More Detail</span></div><div class="stars">★★★★★</div>
  </div>
  <div class="product">
    <div class="ph" role="img" aria-label="White smartphone" style="width:70px;height:62px;margin:0 auto;background:linear-gradient(135deg,#eef2f6,#b7c3cf);border-radius:6px"></div>
    <p class="name">Lorem Ipsum<br>Dolor Consectetur</p><p class="price">$900</p>
    <div class="btns"><span class="btn btn-red">Add to Cart</span><span class="btn btn-blue">More Detail</span></div><div class="stars">★★★★★</div>
  </div>
</section>

<section class="abs triple activity card">
  <div class="ph" role="img" aria-label="Laptop and phone showing the store" style="width:125px;height:95px;margin:12px auto 0;background:linear-gradient(#e6ebf0,#8f99a3)"></div>
  <h4>ACTIVITY STREAM</h4>
  <p>Lorem ipsum dolor sit amet, consectetur adipisicing elit, sed do eiusmod tempor incididunt ut labore et dolore magna aliqua.</p>
</section>

<section class="abs triple tollfree card">
  <div class="ph" role="img" aria-label="Support agents wearing headsets" style="width:152px;height:104px;background:linear-gradient(135deg,#cfdbe6,#8aa3b8)"></div>
  <p class="lbl">CALL US TOLL FREE:</p>
  <p class="num"><svg width="10" height="11" viewBox="0 0 24 24"><path fill="#0b63b0" d="M6.6 10.8a15 15 0 0 0 6.6 6.6l2.2-2.2c.3-.3.7-.4 1-.2 1.1.4 2.3.6 3.6.6.6 0 1 .4 1 1V20c0 .6-.4 1-1 1A17 17 0 0 1 3 4c0-.6.4-1 1-1h3.5c.6 0 1 .4 1 1 0 1.3.2 2.5.6 3.6.1.3 0 .7-.2 1z"/></svg>+484 - 555 - 0142</p>
  <p class="mail">info@qbbrightpathsolutions.com</p>
</section>

<section class="abs triple testi card">
  <svg class="abs" style="right:0;top:0" width="32" height="16"><polygon points="0,0 32,0 32,16 10,16" fill="#0b63b0"/><path d="M22 5l-3 3 3 3" stroke="#fff" fill="none" stroke-width="1.5"/></svg>
  <div class="ph abs" role="img" aria-label="Customer portrait" style="left:15px;top:15px;width:45px;height:43px;background:linear-gradient(#c9b39e,#7a6350)"></div>
  <div class="who"><b>Daniel Reyes</b><span>Posted on 13 July 2013<br>Australia, Sydney</span></div>
  <span class="quote" style="left:14px;top:72px">“</span>
  <p>Lorem ipsum dolor sit amet, consectetur adipisicing elit, sed do eiusmod tempor incididunt ut labore et dolore magna aliqua. Ut enim ad minim veniam, quis nostrud exercitation ullamco laboris nisi ut aliquip ex ea commodo consequat. Duis aute irure dolor in reprehenderit in voluptate velit esse</p>
  <span class="quote" style="left:128px;top:150px">”</span>
</section>

<section class="abs news card">
  <div style="position:absolute;left:20px;top:11px;width:230px">
    <h4>LATEST NEWS</h4>
    <div class="item"><div class="ph" role="img" aria-label="Author portrait" style="width:19px;height:18px;flex:none;background:#b49a85"></div><div><b>Consec elit tetur adipisicing elit</b><br>Lorem ipsum dolor sit Consec elit tetur adipisicing elit lorem<br>20 July, 2013 &nbsp;| &nbsp;<span class="red">Read More</span></div></div>
    <div class="item"><div class="ph" role="img" aria-label="Author portrait" style="width:19px;height:18px;flex:none;background:#b49a85"></div><div><b>Consec elit tetur adipisicing elit</b><br>Lorem ipsum dolor sit Consec elit tetur adipisicing elit lorem<br>20 July, 2013 &nbsp;| &nbsp;<span class="red">Read More</span></div></div>
  </div>
  <div class="tw">
    <h4>CHIRPER TWITS</h4>
    <div style="display:flex;gap:4px;margin-top:6px">
      <span style="width:14px;height:14px;border-radius:50%;background:var(--sky);flex:none;margin-top:2px"></span>
      <div><p class="tw-title">Ut enim ad minim veniam</p><p class="tw-body">Quis nostrud exercitation ullamco laboris nisi ut aliquip ex ea commodo consequat. Duis aute irure dolor in reprehenderit in <span style="color:#aaa;font-style:italic">2 hour ago . Reply</span></p></div>
    </div>
    <div style="position:absolute;left:138px;top:76px;display:flex;gap:6px">
      <span class="arrow" style="width:18px;height:18px;border-color:#ccc"><span style="width:11px;height:11px;background:#777"></span></span>
      <span class="arrow" style="width:18px;height:18px"><span style="width:11px;height:11px"></span></span>
    </div>
  </div>
</section>

<footer class="abs footer">
  <div class="fcol" style="left:56px"><h5>ABOUT US</h5>
    <ul><li>Home</li><li>Hardware</li><li>Software</li><li>Services</li><li>Contact</li></ul></div>
  <div class="fcol" style="left:122px"><h5>LATEST PRODUCTS</h5>
    <div class="thumbs">
      <span class="ph" role="img" aria-label="Phone product" style="background:#7f96aa"></span>
      <span class="ph" role="img" aria-label="Phone product" style="background:#7f96aa"></span>
      <span class="ph" role="img" aria-label="Phone product" style="background:#7f96aa"></span>
      <span class="ph" role="img" aria-label="Phone product" style="background:#7f96aa"></span>
      <span class="ph" role="img" aria-label="Phone product" style="background:#7f96aa"></span>
      <span class="ph" role="img" aria-label="Phone product" style="background:#7f96aa"></span>
    </div></div>
  <div class="fcol" style="left:258px"><h5>NEWSLETTER SIGNUP</h5>
    <p style="font-size:6.3px;line-height:1.3">Adipisicing elit Lorem ipsum<br>dolor sit consectetur..</p>
    <div class="field">Enter Email</div><div class="sub">Subscribde Now</div></div>
  <div class="fcol" style="left:372px"><h5>FRIENDBOOK PLUGING</h5>
    <div class="fbox">
      <div style="display:flex;gap:4px;align-items:center"><span style="width:18px;height:18px;border-radius:50%;background:var(--blue)"></span><span>Q.B. Brightpath Solutions<br><span style="border:1px solid #ccc;padding:0 2px">Like</span></span></div>
      <p style="margin-top:5px;border-top:1px solid #eee;padding-top:3px">10,895 people like QBBrightpathSolutions</p>
      <div style="display:flex;gap:3px;margin-top:3px">
        <span class="ph" role="img" aria-label="Follower" style="width:20px;height:20px;background:#9a8a7a"></span>
        <span class="ph" role="img" aria-label="Follower" style="width:20px;height:20px;background:#a08c5a"></span>
        <span class="ph" role="img" aria-label="Follower" style="width:20px;height:20px;background:#6d6d6d"></span>
        <span class="ph" role="img" aria-label="Follower" style="width:20px;height:20px;background:#556b5a"></span>
        <span class="ph" role="img" aria-label="Follower" style="width:20px;height:20px;background:#444"></span>
      </div>
      <p style="display:flex;gap:9px;margin-top:1px">Lorem<span>Ipsum</span><span>Doe</span><span>Marcus</span></p>
      <p style="margin-top:4px;border-top:1px solid #eee;padding-top:3px">Friendbook social Plug</p>
    </div></div>
  <div class="fcol" style="left:525px"><h5>CONTACT US</h5>
    <div class="ph" role="img" aria-label="Street map of the office location" style="width:109px;height:93px;background:linear-gradient(135deg,#dfe7d9,#a9c5dc)"></div></div>
</footer>

<div class="abs bottom">
  <span>Copyright © 2013, QBBrightpathSolutions.com, All Rights Reserved. Designed by Brightlineweb.com</span>
  <div class="pay"><span></span><span></span><span></span><span></span><span></span></div>
</div>

</body>
</html>
```